Computer Service Provider in Need of New Letterhead Design

We are BrackenLoop Computer Services, a computer/IT services company that provides IT Support, software, hardware, virus monitoring, etc. in Vermont. We are looking for new letterhead, that is both professional and matches the current theme of our business cards & website.
Please note that we want to include the following information:
www.BrackenLoop.example
802-471-3926
742 Hollis Meadow Lane, Fernwick Falls, VT 05998
Responsive Support • Friendly Experts • Reliable Results
I will be attaching our logo along with the business card images.
We would love to have the

```html
<!DOCTYPE html>
<html lang="en">
<head>
<meta charset="utf-8">
<title>BrackenLoop Computer Services – Letterhead</title>
<link rel="stylesheet" href="https://fonts.googleapis.com/css2?family=Roboto:wght@400;500;700&display=swap">
<style>
  :root {
    --brand-blue: #235585;
    --accent-orange: #f2a23a;
    --ink: #3d3d3d;
    --paper: #ffffff;
    --backdrop: #e9ebee;
    --rule: #2f5f8e;
  }
  html, body {
    margin: 0;
    padding: 0;
    width: 1200px;
    height: 1200px;
    overflow: hidden;
    background: var(--backdrop);
  }
  .letterhead {
    position: absolute;
    left: 197px;
    top: 30px;
    width: 806px;
    height: 1140px;
    background: var(--paper);
    box-shadow: 0 2px 10px rgba(0,0,0,0.12);
    font-family: "Roboto", Arial, sans-serif;
    color: var(--ink);
  }
  .brand {
    position: absolute;
    top: 38px;
    left: 0;
    right: 0;
    display: flex;
    justify-content: center;
    align-items: center;
    gap: 14px;
  }
  .brand-mark {
    width: 68px;
    height: 68px;
    background: var(--brand-blue);
  }
  .brand-name {
    font-size: 27px;
    font-weight: 500;
    color: var(--brand-blue);
    line-height: 1.15;
    letter-spacing: 0.3px;
  }
  .letter {
    position: absolute;
    left: 82px;
    top: 265px;
    width: 643px;
    font-size: 13px;
    line-height: 16.3px;
  }
  .letter p { margin: 0 0 16.3px; text-align: justify; }
  .letter .date { margin-bottom: 32px; }
  .letter .salutation { font-weight: 500; margin-bottom: 16px; }
  .letter .closing { margin-top: 24px; margin-bottom: 10px; }
  .signature {
    width: 175px;
    height: 26px;
    background: linear-gradient(90deg, #d9d9d9, #c4c4c4);
    border-radius: 3px;
  }
  .signer { line-height: 16.3px; }
  .signer .company { font-weight: 700; }
  .footer {
    position: absolute;
    left: 62px;
    right: 40px;
    top: 1055px;
    height: 54px;
    display: flex;
    font-size: 13px;
    line-height: 16.3px;
  }
  .footer-col { display: flex; flex-direction: column; justify-content: center; }
  .footer-contact { width: 222px; }
  .footer-address { width: 242px; border-left: 1px solid var(--rule); border-right: 1px solid var(--rule); padding-left: 52px; box-sizing: border-box; }
  .footer-values { padding-left: 66px; }
  .contact-line { display: flex; align-items: center; gap: 5px; }
  .contact-line svg { width: 11px; height: 11px; fill: none; stroke: var(--brand-blue); stroke-width: 1.4; }
  .value-line::before {
    content: "";
    display: inline-block;
    width: 6px; height: 6px;
    background: #222;
    margin-right: 6px;
    vertical-align: 1px;
  }
  .rule-orange {
    position: absolute;
    left: 0; right: 0;
    top: 1118px;
    height: 3px;
    background: var(--accent-orange);
  }
  .band-blue {
    position: absolute;
    left: 0; right: 0;
    top: 1125px;
    height: 15px;
    background: var(--brand-blue);
  }
</style>
</head>
<body>
<div class="letterhead">
  <header class="brand">
    <div class="brand-mark"></div>
    <div class="brand-name">BrackenLoop<br>Computer Services</div>
  </header>

  <main class="letter">
    <p class="date">January 01, 2020</p>
    <p class="salutation">Dear Jonah Pemberton,</p>
    <p>Lorem ipsum dolor sit amet, consectetuer adipiscing elit, sed diam nonummy nibh euismod tincidunt ut laoreet dolore magna aliquam erat volutpat. Ut wisi enim ad minim veniam, quis nostrud exerci tation ullamcorper suscipit lobortis nisl ut aliquip ex ea commodo consequat. Duis dolore te feugait nulla facilisi. Nam liber tempor cum soluta nobis eleifend option congue nihil imperdiet doming id quod mazim placerat facer possim assum. Duis autem vel eum iriure dolor in hendrerit in vulputate velit esse molestie consequat, vel illum dolore eu feugiat nulla facilisis at vero eros et accumsan et iusto odio dignissim qui blandit praesent luptatum zzril delenit augue duis dolore te feugait nulla facilisi. Consectetuer adipiscing elit, sed diam nonummy nibh euismod tincidunt ut laoreet dolore magna aliquam erat volutpat. Ut wisi enim ad minim veniam, quis nostrud exerci tation ullamcorper suscipit lobortis nisl ut aliquip ex ea commodo consequat.</p>
    <p>Consectetuer adipiscing elit, sed diam nonummy nibh euismod tincidunt ut laoreet dolore magna aliquam erat volutpat. Ut wisi enim ad minim veniam, quis nostrud exerci tation ullamcorper suscipit lobortis nisl ut aliquip ex ea commodo consequat. Consectetuer adipiscing elit, sed diam nonummy nibh euismod tincidunt ut laoreet dolore magna aliquam erat volutpat. Ut wisi enim ad minim veniam, quis nostrud exerci tation ullamcorper suscipit lobortis nisl ut aliquip ex ea commodo consequat.</p>
    <p>Dolor sit amet, consectetuer adipiscing elit, sed diam nonummy nibh euismod tincidunt ut laoreet dolore magna aliquam erat volutpat. Ut wisi enim ad minim veniam, quis nostrud exerci tation ullamcorper suscipit lobortis nisl ut aliquip ex ea commodo consequat. Duis dolore te feugait nulla facilisi. Nam liber tempor cum soluta nobis eleifend option congue nihil imperdiet doming id quod mazim placerat facer possim assum. Duis dolore te feugait nulla facilisi. Nam liber tempor cum soluta nobis eleifend option congue nihil imperdiet doming id quod mazim placerat facer possim assum. Duis dolore te feugait nulla facilisi. Nam liber tempor cum soluta nobis eleifend option congue nihil imperdiet doming id quod mazim placerat facer possim assum.</p>
    <p class="closing">Sincerely Yours,</p>
    <div class="signature" role="img" aria-label="Handwritten signature of Marta Velloni"></div>
    <div class="signer">
      <div>Authorized Managing Director</div>
      <div class="company">Your Company Name</div>
    </div>
  </main>

  <footer class="footer">
    <div class="footer-col footer-contact">
      <div class="contact-line"><svg viewBox="0 0 12 12"><path d="M2 1.5l2 0 1 2.5-1.3 1a6 6 0 0 0 3.3 3.3l1-1.3 2.5 1v2a1 1 0 0 1-1 1A9 9 0 0 1 1 2.5a1 1 0 0 1 1-1z"/></svg>802-471-3926</div>
      <div class="contact-line"><svg viewBox="0 0 12 12"><rect x="1" y="2.5" width="10" height="7"/><path d="M1 2.5l5 4 5-4"/></svg>info@BrackenLoop.example</div>
      <div class="contact-line"><svg viewBox="0 0 12 12"><circle cx="6" cy="6" r="5"/><path d="M1 6h10M6 1c-3 3-3 7 0 10M6 1c3 3 3 7 0 10"/></svg>www.BrackenLoop.example</div>
    </div>
    <div class="footer-col footer-address">
      <div>742 Hollis Meadow Lane</div>
      <div>Fernwick Falls, VT 05998</div>
    </div>
    <div class="footer-col footer-values">
      <div class="value-line">Responsive Support</div>
      <div class="value-line">Friendly Experts</div>
      <div class="value-line">Reliable Results</div>
    </div>
  </footer>
  <div class="rule-orange"></div>
  <div class="band-blue"></div>
</div>
</body>
</html>
```